Pinegate Marketing 8 page broshure

I need a design for an 8 page 8.5 X 11 booklet for my company. Our company colors are dark blue, light blue, and white. I am uploading some files for language that you may use. One of the files is our logo. please use the phrase: To us business is a contact sport as well as Pinegate Marketing is your complete marketing solution. Include something about we offer web and brochure design.as well as social media marketing.

Dear Velkan at Artisan Bazaar, Dear Velkan, we just spoke on the phone about my project for Pinegate Marketing Group sales brochure. As we discussed there are several things wrong with the final version that the Tumble sent to me. First of all the design is completely wrong, It is designed to be 8.5 x 11 when it should be designed to be 8.5 X 5.5 and the fold in the booklet should be the 8.5 side. In other words if you take and 8.5 x 11 piece of paper and fold in half that makes a booklet of 8.5 x 5.5. The other problem that were having with this is that there is no page covering our CRM product which is very important to our service offerings. I have sent you files that cover the CRM but for some reason it wasn't put in. Two small changes, on the front cover I see that we have on the very bottom of the of the page there is a line that says as well as Pinegate marketing is your complete marketing solution. I would like that line taken out. On the back cover I would like to change the address at the very bottom of the page the new address will be 41957 Kimber Ave., Westlake, OH 44163 I think if those changes are made we are about ready to go. Don't misunderstand we love your work, you guys have worked hard and the design is very good there just so's changes to make. Thank you very much, Oliver Marsh

Target Market(s)

Any business that needs help with increasing their sales and marketing in their company. We also have a fully customizable CRM so they may track the leads that are in their pipeline as well as those leads we bring in to their pipeline. On the marketing side we offer many services. Two things that I could not download was we do website design srvices and social media marketing.

Industry/Entity Type

It Company

Font styles to use
Sans Serif

Colors
0555a3
00a990
ffffff

Requirements
Must have
• Company logo on front cover, Stress the various services we offer on the marketing side, stress the CRM - very important. Feel free to use any of the dowloads I am sending to you for text.
Nice to have
• Very professional and elegant presentation.
Should not have
• Should not have any drawings or things that look out of place. Stock picture are fine as long as they have something to do with marketing or CRM.

```html
<!DOCTYPE html>
<html lang="en">
<head>
<meta charset="utf-8">
<title>Pinegate Marketing Group – Brochure Pages 6 &amp; 7</title>
<link rel="stylesheet" href="https://fonts.googleapis.com/css2?family=Arimo:wght@400;700&display=swap">
<style>
  :root {
    --brand-blue: #1b8fd6;
    --brand-blue-deep: #1580c4;
    --paper: #ffffff;
    --ink: #1f1f1f;
    --backdrop: #e6e6e6;
    --on-blue: #ffffff;
  }
  * { box-sizing: border-box; margin: 0; padding: 0; }
  html, body { width: 1200px; height: 800px; overflow: hidden; }
  body {
    background: var(--backdrop);
    font-family: "Arimo", Arial, sans-serif;
    color: var(--ink);
    position: relative;
  }
  .spread {
    position: absolute;
    left: 60px; top: 20px;
    width: 1080px; height: 760px;
    display: flex;
  }
  .page {
    position: relative;
    width: 540px; height: 760px;
    background: var(--paper);
    overflow: hidden;
  }
  p { font-size: 10.3px; line-height: 1.27; text-align: justify; }
  /* Left page */
  .lead-cost {
    position: relative;
    height: 372px;
    padding: 40px 30px 0 32px;
  }
  .lead-cost__backdrop {
    position: absolute;
    left: 160px; top: 95px;
    width: 190px; height: 190px;
    border-radius: 50%;
    background: radial-gradient(circle at 45% 40%, #eef3f9 0%, #dfe7f1 55%, #f6f8fb 100%);
    opacity: .7;
  }
  .lead-cost > *:not(.lead-cost__backdrop) { position: relative; }
  .section-title {
    font-weight: 400;
    font-size: 22px;
    letter-spacing: .2px;
    text-align: center;
    margin-bottom: 6px;
  }
  .lead-cost .section-title { color: var(--brand-blue); }
  .lead-cost p + p { margin-top: 13px; }
  .telecontact {
    height: 388px;
    background: var(--brand-blue);
    color: var(--on-blue);
    padding: 10px 30px 0 32px;
  }
  .telecontact .section-title { margin-bottom: 10px; }
  .telecontact p + p { margin-top: 13px; }
  .telecontact .indent { text-indent: 16px; }
  /* Right page */
  .training { padding: 48px 78px 0 20px; }
  .training p + p { margin-top: 13px; }
  .training__heading {
    color: var(--brand-blue);
    font-weight: 400;
    font-size: 16.5px;
    margin: 14px 0 9px;
  }
  .solution { margin-bottom: 8px; }
  .solution__title {
    color: var(--brand-blue);
    font-weight: 400;
    font-size: 12.4px;
    margin-bottom: 1px;
  }
  .section-tab {
    position: absolute;
    right: 0; top: 0;
    width: 46px; height: 480px;
  }
  .section-tab__label {
    position: absolute;
    right: 0; top: 48px;
    width: 46px; height: 380px;
    writing-mode: vertical-rl;
    color: var(--on-blue);
    font-size: 19px;
    letter-spacing: .3px;
    display: flex; align-items: center; justify-content: flex-start;
  }
  .gutter {
    position: absolute; left: 0; top: 0; bottom: 0; width: 40px;
    background: linear-gradient(90deg, rgba(0,0,0,.08), rgba(0,0,0,0));
  }
</style>
</head>
<body>
<main class="spread">
  <section class="page page--left">
    <div class="lead-cost">
      <div class="lead-cost__backdrop" role="img" aria-label="Faint globe image behind the text"></div>
      <h2 class="section-title">COMPARE THE COST OF A LEAD</h2>
      <p>We have asked our clients to share with us what they have been spending per lead before they discovered what Pinegate Marketing Group could do for them.</p>
      <p>Recently, there was a client who spent $20,000 on a trade show that produced approximately 100 business card leads for their sales people to follow up on. Of the 100 business card leads only 10%, which is a typical average, were usable, closable leads. That averages out to be $2,000 per lead.</p>
      <p>After polling our clients we have compiled information which is quite staggering but not surprising to us. The average cost per lead for usable and closable leads that meet the criteria using traditional methods such as sales calls, trade shows, direct mail etc… The price per lead was $3,995.00</p>
      <p>We also polled our clients and received the following information that is also staggering but not surprising to us. The cost per usable and closable sales leads from Pinegate Marketing Group has been $467.50.</p>
      <p>The cost of traditional methods of advertising by our clients was more than 8 S times higher vs the Pinegate Marketing group results. Another way to look at it is that clients were able to cut their marketing budget by more than 850% to obtain the same amount of leads as they had in the past.</p>
    </div>
    <div class="telecontact">
      <h2 class="section-title">THE EXECUTIVE TELECONTACT TEAM</h2>
      <p>Pinegate Marketing does not believe that traditional telemarketing works as a vehicle to represent expensive, vertical products and services. Think about it. . . what chance does an $8 $12 per hour telemarketer, reading a script, have trying to present a $50,000 to $1,000,000 product or a service contract worth millions of dollars to the VP of Finance or CFO of a fortune 1000 company? Pinegate’s “Solutions Marketing” programs create an entirely new paradigm which goes far beyond traditional telemarketing. In addition to having our clients meet and assist in training our Account manager staff, we specialize in overcoming sales objections and beginning the consultative sales process.</p>
      <p class="indent">Because Pinegate pays possibly the highest rates in the industry and treats our staff like “family”, we are able to attract and keep the best possible telecontact personnel. This allows us to provide the greatest possible value to our clients. Many tell Pinegate Marketing how favorably impressed they are by the caliber of the Pinegate Account Manager team.</p>
      <p>Utilizing lead generation personnel of this caliber allows Pinegate Marketing to conduct “top down” Solutions Marketing” calls where Pinegate’s Account Managers track down and conduct non scripted, peer to peer dialogues with senior level personnel at targeted companies. This provides our clients more return on their investment. Any company can discover the “easy” leads where the prospect immediately expresses their interest. The added value Pinegate brings is our ability to overcome sales objections, understand what is going on “between the lines”, and create highly qualified leads where the opportunity did not present itself at the beginning of the prospect interview.</p>
    </div>
  </section>

  <section class="page page--right">
    <div class="gutter"></div>
    <div class="training">
      <p>Training is where ideal solutions meet day to day reality. In this reality, even perfect technologies and processes lose value unless employees are prepared to deliver consistently and completely. Employee training programs must address a client’s business objectives and solve business problems. At the same time, they must engage employees in ways that work.</p>
      <p>We have extensive experience building well organized and actionable training programs for every area of business. Whether you need training support for a major change effort, an employee development initiative, or just to enhance your current training programs, we know how to break down even the most complex ideas in ways that make them easy for people to understand.</p>
      <h3 class="training__heading">Our Training solutions include:</h3>
      <div class="solution">
        <h4 class="solution__title">Training Design</h4>
        <p>Training Design must outline a curriculum and set plans for the who, what, where, when, why and how of training. We collaborate with our clients to design training programs that meet the needs of their organization and end users. Our approach integrates proven training methods with adult learning psychology to design training programs and assets that build institutional value.</p>
      </div>
      <div class="solution">
        <h4 class="solution__title">Training Development</h4>
        <p>Brightwell’s Training doesn’t just rehash a user manual; it creates an environment in which people learn how to use new processes and systems to do their jobs. We work with our clients to develop the right combination of pre work, instructor led, web based, and practice exercises to ensure the availability and usability of training at every location.</p>
      </div>
      <div class="solution">
        <h4 class="solution__title">Training Delivery</h4>
        <p>Training is delivered using a just in time approach that enables individuals to learn skills close to the time when they will be needed. Role based modules provide learners with the information that they need and balances their training time with their job requirements. Brightwell works to coordinate training, design attendance rosters and execute sessions to ensure the quality and effectiveness of the training. Our training approach has supported hundreds of employees and complex schedules across multiple locations.</p>
      </div>
      <div class="solution">
        <h4 class="solution__title">Train the Trainer</h4>
        <p>Our Train the Trainer Method plays a critical role in ensuring that our clients’ trainers have the skills and knowledge to lead the training programs as they were designed. Our training experts teach your training leaders how to transform employees so their success continues beyond the classroom.</p>
      </div>
      <div class="solution">
        <h4 class="solution__title">Learning Assessment (User Adoption)</h4>
        <p>Training would not be complete without tracking the results. Brightwell develops evaluation strategies and tools that measure the real success of the training program the learners’ ability to achieve business objectives. Our Learning Assessments are custom made to shed light on user adoption, employee performance and areas for improvement.</p>
      </div>
      <div class="solution">
        <h4 class="solution__title">Training Program Effectiveness</h4>
        <p>Our deep experience in Organizational Learning makes us a valuable partner in evaluating existing training programs. Whether you need to update your current program or would just like an independent, expert opinion, Brightwell can quickly determine the strengths, weaknesses, and risks associated with your training and identify practical opportunities for improvement.</p>
      </div>
    </div>
    <svg class="section-tab" viewBox="0 0 46 480" aria-hidden="true">
      <polygon points="0,0 46,0 46,480 0,455" fill="var(--brand-blue)"/>
    </svg>
    <div class="section-tab__label">SALES CONSULTING AND TRAINING</div>
  </section>
</main>
</body>
</html>
```